New business blog needs wordpress theme

I need a unique wordpress theme for my new business oriented blog at hollowpeakdesk.com. The blog focuses on my experience as an entrepreneur and offers insights into business problems while chronicling my experience building a new company.

I would like to see a theme that looks more like a creative professional's website, not a business website. Large photos, bright colors, unique layout. I do not want stock photos of people in suits doing business type things. Also, no pictures of me - I am blogging anonymously.

The design should communicate technology and beauty - for example, I really like the feel of the landing page at www.tundrelo.com - it is beautiful to look at but also reflects the cutting edge nature of what they are doing.

Industry/Entity Type

Business

```html
<!DOCTYPE html>
<html lang="en">
<head>
<meta charset="utf-8">
<title>Busy Rowan – Small business blog</title>
<link href="https://fonts.googleapis.com/css2?family=Source+Sans+3:ital,wght@0,400;0,600;0,700;1,400&display=swap" rel="stylesheet">
<style>
:root{
  --teal:#16979a;
  --teal-dark:#0f7f83;
  --orange:#f08a1c;
  --orange-dark:#d9750d;
  --page:#e9e9e9;
  --card:#ffffff;
  --line:#dcdcdc;
  --text:#555555;
  --muted:#8a8a8a;
  --white:#ffffff;
}
*{box-sizing:border-box;margin:0;padding:0}
html,body{width:1200px;height:2601px;overflow:hidden}
body{background:var(--page);font-family:"Source Sans 3",Arial,sans-serif;color:var(--text);position:relative}
a{color:inherit;text-decoration:none}

.site-header{position:absolute;left:0;top:0;width:1200px;height:87px;background:var(--teal);border-bottom:6px solid var(--orange)}
.brand{position:absolute;left:152px;top:22px;font-size:26px;font-weight:700;color:var(--white)}
.main-nav{position:absolute;right:148px;top:28px;display:flex;gap:8px}
.main-nav a{font-size:14px;color:var(--white);padding:4px 12px;border-radius:3px}
.main-nav a.current{background:var(--orange)}

.hero{position:absolute;left:0;top:87px;width:1200px;height:421px;background:linear-gradient(120deg,#6f7f86 0%,#c9d4d8 35%,#e6ecee 60%,#5c8c9c 85%,#9fb8c0 100%)}
.hero-caption{position:absolute;left:147px;top:281px;width:564px;height:80px;background:rgba(22,151,154,.85);color:var(--white);font-size:19px;font-weight:600;line-height:28px;padding:12px 18px}
.hero-arrow{position:absolute;top:177px;width:31px;height:31px;background:var(--orange)}
.hero-arrow.prev{left:0}.hero-arrow.next{right:0}
.hero-arrow svg{display:block;margin:8px auto}

.post{position:absolute;left:147px;width:581px}
.post-image{height:281px;border:6px solid var(--white);box-shadow:0 1px 3px rgba(0,0,0,.2)}
.post-body{margin-top:11px;background:var(--card);box-shadow:0 1px 3px rgba(0,0,0,.15);padding:30px 34px 0;position:relative}
.post-body::before{content:"";position:absolute;left:62px;top:-10px;border:10px solid transparent;border-top:0;border-bottom-color:var(--card)}
.post-title{font-size:28px;font-weight:700;color:var(--orange);line-height:31px}
.post-meta{display:flex;justify-content:space-between;font-size:10px;font-style:italic;color:var(--muted);margin:14px 0 28px}
.post-meta .comments{display:flex;align-items:center;gap:10px}
.post-excerpt{font-size:12px;line-height:21px}
.post-actions{display:flex;align-items:center;height:60px;font-size:10px}
.share{display:flex;align-items:center;margin-right:28px}
.share-btn{border:1px solid #bbb;border-radius:3px;padding:1px 6px;font-weight:700;color:#336}
.share-btn.blue{background:#3b5a97;color:var(--white);border-color:#3b5a97}
.share-count{border:1px solid #bbb;border-radius:2px;padding:1px 5px;margin-left:4px}
.read-more{margin-left:auto;border:1px solid #bbb;border-radius:10px;padding:2px 8px;font-size:11px;display:flex;align-items:center;gap:6px;background:#f4f4f4}

.sidebar{position:absolute;left:749px;top:551px;width:302px;height:614px;background:var(--card);box-shadow:0 1px 3px rgba(0,0,0,.15);padding:36px 26px}
.search{display:flex;border:1px solid var(--line);height:44px;padding:4px}
.search span{flex:1;font-size:10px;color:#aaa;padding:11px 6px}
.search b{background:var(--orange);color:var(--white);width:54px;display:flex;align-items:center;justify-content:center;font-size:13px}
.widget-note{font-size:10px;color:#333;margin-top:10px;line-height:15px}
.widget-title{font-size:16px;font-weight:700;color:var(--orange);margin:42px 0 16px}
.post-list{list-style:none;font-size:11px;color:#333;line-height:18px}
.post-list li{padding-left:12px;position:relative;margin-bottom:14px}
.post-list li::before{content:"›";position:absolute;left:2px}
.post-list small{display:block;font-size:8px;color:var(--muted);line-height:14px}
.link-icons{display:flex;gap:4px}
.link-icons i{width:14px;height:14px;display:block;border-radius:2px}

.older{position:absolute;left:151px;top:2338px;font-size:12px;color:var(--orange);text-decoration:underline}

.site-footer{position:absolute;left:0;top:2389px;width:1200px;height:212px;background:var(--teal);border-top:6px solid var(--orange)}
.footer-text{position:absolute;left:148px;top:50px;width:430px;font-size:11px;line-height:20px;color:#d8eeee}
.newsletter{position:absolute;left:624px;top:55px;width:410px;height:46px;background:var(--white);border-radius:3px;display:flex;align-items:center;padding:0 4px 0 16px;font-size:11px;color:#888}
.newsletter span{flex:1;margin-left:10px}
.newsletter b{background:var(--orange);color:var(--white);padding:8px 14px;font-weight:600}
.social{position:absolute;left:148px;top:127px;display:flex;gap:13px}
.social i{width:44px;height:44px;border-radius:50%;background:var(--orange);display:block}
.copyright{position:absolute;left:625px;top:148px;font-size:10px;color:#b8dede}
</style>
</head>
<body>
<header class="site-header">
  <a class="brand" href="#">Busy Rowan</a>
  <nav class="main-nav">
    <a class="current" href="#">Home</a><a href="#">Small Business</a><a href="#">Technology</a><a href="#">About Rowan</a><a href="#">Contact</a>
  </nav>
</header>

<section class="hero" role="img" aria-label="Hands touching a tablet with floating glowing cubes showing charts">
  <p class="hero-caption">Rowan talks business. Best practices, articles and tips and about small business in the United States</p>
  <span class="hero-arrow prev"><svg width="10" height="14"><path d="M8 1 2 7l6 6" stroke="#fff" stroke-width="3" fill="none"/></svg></span>
  <span class="hero-arrow next"><svg width="10" height="14"><path d="M2 1l6 6-6 6" stroke="#fff" stroke-width="3" fill="none"/></svg></span>
</section>

<article class="post" style="top:551px">
  <div class="post-image" role="img" aria-label="Finger touching glowing communication icons" style="background:radial-gradient(circle at 60% 40%,#4a7aa8,#0d1c35 70%)"></div>
  <div class="post-body">
    <h2 class="post-title">Comparing Direct Mail to Dealbunch – By the Numbers</h2>
    <div class="post-meta"><span>Posted on March 6, 2014 by Rowan</span><span class="comments"><svg width="12" height="10"><path d="M1 1h10v6H5L2 9V7H1z" fill="none" stroke="#999"/></svg>Leave a comment</span></div>
    <p class="post-excerpt">Unhappy with the results of a direct mail (snail mail) campaign, I decided to compare the results to a Dealbunch campaign. I compared both the cost of the respective campaigns, the revenue generated, the customers acquired and customer retention.</p>
    <div class="post-actions">
      <span class="share"><span class="share-btn">Post</span><span class="share-count">1</span></span>
      <span class="share"><span class="share-btn blue">Like</span><span class="share-count">0</span><span class="share-btn" style="margin-left:6px;color:#c33">+1</span><span class="share-count">0</span></span>
      <a class="read-more" href="#">Read More <svg width="10" height="10"><circle cx="5" cy="5" r="5" fill="#333"/><path d="M4 3l2 2-2 2" stroke="#fff" fill="none"/></svg></a>
    </div>
  </div>
</article>

<article class="post" style="top:1143px">
  <div class="post-image" role="img" aria-label="Laptop, keyboard and mouse over a blue digital grid" style="background:linear-gradient(135deg,#0f4a63,#3aa3c0 50%,#0e5670)"></div>
  <div class="post-body">
    <h2 class="post-title">Finally Dumping Chatterloop on Pocketos – Any Recommendations for an SMS App?</h2>
    <div class="post-meta"><span>Posted on March 6, 2014 by Rowan</span><span class="comments"><svg width="12" height="10"><path d="M1 1h10v6H5L2 9V7H1z" fill="none" stroke="#999"/></svg>Leave a comment</span></div>
    <p class="post-excerpt">I am embarrassed how long I tried to make Chatterloop on Pocketos work. Chatterloop is Orbix's default SMS client for Pocketos Maplebar. It combines SMS with Orbix's chat/video product .</p>
    <div class="post-actions">
      <span class="share"><span class="share-btn">Post</span><span class="share-count">1</span></span>
      <span class="share"><span class="share-btn blue">Like</span><span class="share-count">0</span><span class="share-btn" style="margin-left:6px;color:#c33">+1</span><span class="share-count">0</span></span>
      <a class="read-more" href="#">Read More <svg width="10" height="10"><circle cx="5" cy="5" r="5" fill="#333"/><path d="M4 3l2 2-2 2" stroke="#fff" fill="none"/></svg></a>
    </div>
  </div>
</article>

<article class="post" style="top:1732px">
  <div class="post-image" role="img" aria-label="Abstract blue molecule with data markers" style="background:linear-gradient(135deg,#2f8fae,#a9d3df 55%,#4e9bb2)"></div>
  <div class="post-body">
    <h2 class="post-title">The Who &amp; The Why</h2>
    <div class="post-meta"><span>Posted on March 5, 2014 by Rowan</span><span class="comments"><svg width="12" height="10"><path d="M1 1h10v6H5L2 9V7H1z" fill="none" stroke="#999"/></svg>1 Comment</span></div>
    <p class="post-excerpt">I started this blog to share much of the knowledge that I have built up during the last 20 years as an entrepreneur. With all of my businesses, I continually run experiments on what works best. I usually summarize my results in little notes to myself – my hope is to share much of that with you. I also hope to learn a lot from the community of entrepreneurs out there.</p>
    <div class="post-actions">
      <span class="share"><span class="share-btn">Post</span><span class="share-count">1</span></span>
      <span class="share"><span class="share-btn blue">Like</span><span class="share-count">0</span><span class="share-btn" style="margin-left:6px;color:#c33">+1</span><span class="share-count">0</span></span>
      <a class="read-more" href="#">Read More <svg width="10" height="10"><circle cx="5" cy="5" r="5" fill="#333"/><path d="M4 3l2 2-2 2" stroke="#fff" fill="none"/></svg></a>
    </div>
  </div>
</article>

<aside class="sidebar">
  <div class="search"><span>Search Here</span><b>Go</b></div>
  <p class="widget-note">Ut eget metus nibh, nec scelerisque sem. Nulla dui purus, pellentesque sit amet rutrum vitae.</p>
  <h3 class="widget-title">Recent Posts</h3>
  <ul class="post-list">
    <li>Ut eget metus nibh, nec scelerisque sem. Nulla dui purus, pellentesque sit amet rutrum vitae<small>14th February 2014</small></li>
    <li>Fusce augue arcu, volutpat eu facilisis suscipit, venenatis vehicula diam.<small>12th February 2014</small></li>
    <li>Ut eget metus nibh, nec scelerisque sem. Nulla dui purus, pellentesque sit amet rutrum vitae<small>14th February 2014</small></li>
  </ul>
  <h3 class="widget-title" style="margin-top:28px">Top Posts by Clicks</h3>
  <ul class="post-list"><li>hollowpeakdesk.com</li></ul>
  <h3 class="widget-title" style="margin-top:28px">Links</h3>
  <div class="link-icons"><i style="background:#3b5a97"></i><i style="background:#d44"></i><i style="background:#3a9ad9"></i><i style="background:#2b5e9e"></i><i style="background:var(--orange)"></i></div>
</aside>

<a class="older" href="#">&lt;&lt; Older Entries</a>

<footer class="site-footer">
  <p class="footer-text">Quisque turpis lorem, vehicula eget rhoncus vel, ultricies ac mauris. Morbi lectus velit, tincidunt congue pharetra eu, varius nec libero. Vivamus justo risus, dignissim ac vestibulum eget, egestas rutrum magna. Etiam malesuada nisi et nisl volutpat tristique.</p>
  <div class="newsletter"><svg width="12" height="9"><rect x=".5" y=".5" width="11" height="8" fill="none" stroke="#aaa"/><path d="M1 1l5 4 5-4" stroke="#aaa" fill="none"/></svg><span>Join Our Newsletter Here</span><b>Join</b></div>
  <div class="social"><i></i><i></i><i></i></div>
  <p class="copyright">Copyright 2014 Busy Rowan &nbsp;|&nbsp; All rights reserved.</p>
</footer>
</body>
</html>
```